EXCITING DECK for Automotive dealers that shows how our Technology works.

General Concept
The deck should visually represent the Trade and Credit Lead Life Cycle program is a dynamic, interconnected journey, illustrating how leads are generated, nurtured, and converted. The focus should be on how your system flows seamlessly between credit and trade-in opportunities for consumers, with the goal of maximizing engagement and conversions.
Slide 1: Title Slide - Lead Life Cycle Program
• Visual Concept: A stylized cycle or wheel that represents the stages of the lead life cycle, with arrows connecting each stage.
• Headline: "Lead Life Cycle Program"
• Subhead line: "Credit Pre-Qualification and Trade-In Appraisal"
• Imagery: Modern, sleek graphics of vehicles, smartphones (for texting), email icons, and dollar signs for value.
Slide 2: Lead Generation Sources
• Visual Concept: A funnel with the top representing the different lead generation sources.
• Content:
o Top of Funnel (Leads Enter):
 Pre-Qualification Tool (Fast4Loan)- How it Works
 1. Converts Web Traffic into the highest quality lead on the market
 Vorqel Email/Mail Marketing – How it Works
 1. Delivers actionable leads from email marketing not Just OPENS AND CLICKS. Show the text demo. Audiences below
1. Past Sold Customers (Equity Targets)
2. Past Service Onlu Department Customers (Conquest Sales)
3. Unsold Leads (from previous interactions)
o Each source should have a distinct icon to represent it (e.g., envelope for email, a wrench for past service customers, etc.).
• Headline: "Multiple Lead Sources Feeding into the Program"
• Imagery: The funnel narrowing toward the next step with leads symbolized by icons flowing downward.
Slide 3: Credit Leads - Pre-Qualified Flow
• Visual Concept: A customer engaging with the Fast4Loan tool on their mobile, being pre-qualified, and then us sending a offer to appraise their trade.
• Flow Explanation:
o Customer pre-qualifies via Fast4Loan → Receives credit approval → Email and Mail Example to check trade-in value.
• Headline: "Pre-Qualified Leads: Offering Trade-In Appraisal"
• Imagery: A sequence that shows how a customer moves from pre-qualification to considering their trade-in value. To purchasing
Slide 4: Trade-In Leads - Valuation Flow
• Visual Concept: A customer who has received a trade-in valuation offer now being prompted to pre-qualify for financing.
• Flow Explanation:
o Customer texts for vehicle value → Receives trade-in appraisal → Offer to pre-qualify for financing appears link is at the bottom of the text response.
• Headline: "Trade-In Leads: Offering Credit Pre-Qualification"
• Imagery: A customer looking at their trade-in value on their phone and being shown an additional prompt to pre-qualify for a loan.
Slide 5: Cross-Offer Opportunities
• Visual Concept: A two-way street or cycle, illustrating the seamless transition between offering pre-qualification to trade-in customers and offering trade-in value to credit leads.
• Content:
o Two pathways:
1. Start as a Credit Lead → Offer Trade-In Valuation
2. Start as a Trade-In Lead → Offer Credit Pre-Qualification
o Headline: "Cross-Offer Opportunities for Maximum Engagement"
• Imagery: Arrows going in both directions, symbolizing the back-and-forth opportunities between credit and trade leads.
Digital Retargeting for Cross-Action Engagement
• Visual Concept: An omnichannel approach with a customer in the center, surrounded by email/Mail icons, Chatterbook, and Snapgrove logos. Arrows leading from each platform back to the customer, showing how these channels drive engagement.
• Content:
o Title: "Engage to Convert one lead type to get both with Email/Mail and Digital Retargeting"
o Explanation:
 Whether a lead starts as a Pre-Qualified Credit Lead or a Trade-In Valuation Lead, we use personalized Email/Mail Campaigns and Digital Retargeting Ads (Chatterbook & Snapgrove) to encourage them to take the next action.
 If they pre-qualify for credit, we retarget them with trade-in valuation offers.
 If they start with a trade-in valuation, we follow up with financing offers.
o Headline: "Leverage Email & Social Retargeting to Drive Cross-Action"
• Visuals:
o Icons of Email, Chatterbook, and Snapgrove: Showing the platforms through which you retarget leads.
o Customer Journey Map: Illustrating how leads who interacted once are guided to the next step (credit lead → trade-in offer, trade-in lead → pre-qualification).
o Arrows Flowing Between Channels: Showing how no matter where a lead starts, they are continually engaged through digital touchpoints until they complete both actions.
o Ad examples
• Call to Action: "Stay Top of Mind and Convert Leads into Multi-Action Customers"
This slide emphasizes how you’re leveraging both email/mail marketing and social media retargeting to move leads further along the customer journey, regardless of how they entered your funnel. The visuals should reinforce the idea of continuous engagement and omnipresent reminders for them to take action.
________________________________________
Slide 6: Lifecycle Representation
• Visual Concept: A circular diagram showing how leads can continuously move between credit and trade offers throughout their lifecycle.
• Content:
o Show how the lifecycle doesn’t end after one interaction, but can continue with follow-up offers.
o Headline: "Continuous Engagement Throughout the Lead Life Cycle"
• Imagery: Circular arrows or flowchart representing each stage looping back into the lifecycle, emphasizing that leads can be re-engaged.
Slide 7: Lead Conversion Goals
• Visual Concept: A progression from leads to successful transactions (e.g., a customer with keys to a new car). Showing that getting customers to take both of these actions delives a lead that is very committed to the process of buying.
• Content:
o End goal: Convert both credit and trade leads into sales.
o Show statistics or success metrics as optional data points.
o Headline: "Converting Leads into Sales"
• Imagery: A car dealership handing over keys, happy customers, and sold vehicles.
Slide 8: Next Steps / Call to Action
• Visual Concept: A final slide summarizing the key takeaways and next steps.
• Headline: "Maximize Lead Potential with Cross-Offer Opportunities"
• Imagery: A mix of credit leads, trade leads, and successful customer outcomes.
________________________________________These slides should be clean and modern, using simple but impactful visuals like arrows, icons, and flow diagrams to represent the journey. The key is to emphasize flow and interaction between credit and trade-in opportunities, showing the two-way cross-sell nature of your Lead Life Cycle Program.

I have attached a current deck so you can pull some basic product info and graphics into the new deck (PLEASE DONT JUST COPY THE OLD DECK). I have also included some of our email artwrok if you need it. If you want to look at our website go here www.plorvenadsgroup.example

Target Market(s)

Car Dealers

Industry/Entity Type

Automotive Marketing

Requirements
Must have
• PLEASE READ THE PROJECT DESCRIPTION
Nice to have
Should not have
• PLEASE dont just copy the deck i uploaded. I am looking for a differnt take.

```html
<!DOCTYPE html>
<html lang="en">
<head>
<meta charset="utf-8">
<title>Lead Life Cycle Program – Deck Overview</title>
<link href="https://fonts.googleapis.com/css2?family=Poppins:ital,wght@0,400;0,500;0,600;0,700;1,400&display=swap" rel="stylesheet">
<style>
:root{
  --red:#e5001c;
  --dark:#3a3a3c;
  --grey:#8a8a8c;
  --ink:#2b2b2b;
  --slide:#fdecee;
  --white:#ffffff;
  --green:#4aa01c;
}
*{box-sizing:border-box;margin:0;padding:0}
html,body{width:1105px;height:1200px;overflow:hidden;background:var(--white)}
body{position:relative;font-family:'Poppins',sans-serif;color:var(--ink)}
.slide{position:absolute;width:481px;height:270px;background:var(--slide);overflow:hidden}
.slide > *{position:absolute}
.s1{left:48px;top:27px;background:linear-gradient(120deg,#fbe3dc 0%,#fdf1ee 55%,#fdf4f2 100%)}
.s5{left:577px;top:27px}
.s2{left:48px;top:311px}
.s6{left:577px;top:311px}
.s3{left:48px;top:597px}
.s7{left:577px;top:597px}
.s4{left:48px;top:882px}
.s8{left:577px;top:882px}
.accent-bar{height:4px;width:18px;background:var(--red)}
.accent-bar.center{left:50%;transform:translateX(-50%)}
.heading{font-weight:700;color:var(--ink);line-height:1.05;letter-spacing:.2px}
.heading.center{left:0;width:100%;text-align:center}
.red{color:var(--red)}
.page-no{right:5px;bottom:3px;width:13px;height:13px;border-radius:50%;background:var(--red);color:var(--white);font-size:6px;font-weight:600;display:flex;align-items:center;justify-content:center}
.body-copy{font-size:5.3px;line-height:2.05;color:#444}
/* slide 1 */
.s1 .heading{left:12px;top:84px;font-size:25px}
.s1 .subhead{left:12px;top:146px;font-size:12.5px;line-height:1.55;color:var(--ink)}
.s1 .cycle{left:222px;top:10px;width:250px;height:250px}
/* slide 2 */
.s2 .accent-bar{top:18px}
.s2 .heading{top:30px;font-size:21px}
.funnel{left:0;top:0;width:481px;height:270px}
.source-pill{font-size:8px;font-weight:600;color:var(--white);line-height:1.4;z-index:2}
.source-note{font-size:7.4px;line-height:1.5;color:var(--ink);z-index:2}
.audience{font-size:5px;font-style:italic;line-height:1.95;color:var(--ink)}
.audience b{color:var(--red);font-weight:400}
/* slide 3 */
.s3 .accent-bar{top:19px}
.s3 .heading{top:31px;font-size:21px}
.flow-line{top:156px;height:1.5px}
.step{width:86px;height:86px;border-radius:50%;background:var(--white);box-shadow:0 1px 6px rgba(0,0,0,.12);display:flex;flex-direction:column;align-items:center;justify-content:center;text-align:center;font-size:6.3px;line-height:1.55;color:var(--ink);padding:0 3px;white-space:nowrap}
.step svg{width:28px;height:28px;margin-bottom:6px}
.step-ring{width:100px;height:100px}
/* slide 4 */
.s4 .accent-bar,.s7 .accent-bar,.s8 .accent-bar,.s6 .accent-bar{width:30px}
.s4 .accent-bar{left:12px;top:14px}
.s4 .heading{left:12px;top:25px;font-size:20px}
.journey-node{width:54px;height:54px;border-radius:50%;background:var(--white);display:flex;align-items:center;justify-content:center}
.journey-node svg{width:26px;height:26px}
.journey-label{font-size:10.5px;font-weight:600;line-height:1.2}
.thought{background:var(--red);color:var(--white);border-radius:50%;font-size:9px;font-weight:600;text-align:center;line-height:1.15;display:flex;align-items:center;justify-content:center}
/* slide 5 */
.s5 .accent-bar{top:13px;width:30px}
.s5 .heading{top:23px;font-size:21px}
.col-head{font-size:7.6px;font-weight:600;text-align:center;line-height:1.45;width:150px}
.col-rule{height:1px;width:16px;background:#aaa}
.col-div{width:1px;background:#cfc0c2}
.lead-label{font-size:7.6px;font-weight:700;color:var(--red);text-align:center;width:150px}
.lead-sub{font-size:6px;text-align:center;width:150px}
.map-box{width:72px;height:38px;border:1.2px solid var(--ink);border-radius:13px;background:var(--white);display:flex;flex-direction:column;align-items:center;justify-content:flex-end;padding-bottom:5px;font-size:5.8px;font-weight:700;color:var(--red);text-align:center;line-height:1.1}
.map-box svg{width:13px;height:13px;margin-bottom:2px}
.cta-line{left:0;width:100%;text-align:center;top:241px;font-size:7.4px;font-weight:600}
/* slide 6 */
.s6 .accent-bar{left:10px;top:48px}
.s6 .heading{left:10px;top:59px;font-size:20px}
.s6 .body-copy{left:10px;top:133px;width:225px}
.s6 .cycle{left:252px;top:22px;width:230px;height:230px}
/* slide 7 */
.s7 .photo{left:11px;top:17px;width:212px;height:231px;border-radius:12px;background:linear-gradient(150deg,#5b6f86 0%,#b9c3cc 40%,#e9e3dc 65%,#3d3a3a 100%)}
.s7 .accent-bar{left:240px;top:22px}
.s7 .heading{left:240px;top:31px;font-size:20px}
.s7 .body-copy{left:241px;top:83px;width:222px}
.stat-card{top:157px;width:70px;height:91px;border-radius:10px;background:var(--white);text-align:center}
.stat-card svg{position:absolute;left:27px;top:12px;width:16px;height:14px}
.stat-num{position:absolute;left:0;width:100%;top:30px;font-size:18px;font-weight:700;color:var(--ink)}
.stat-label{position:absolute;left:0;width:100%;top:58px;font-size:7.6px;line-height:1.35;color:var(--ink)}
/* slide 8 */
.s8 .accent-bar{left:12px;top:14px}
.s8 .heading{left:12px;top:24px;font-size:20px}
.s8 .body-copy{left:12px;top:78px;width:276px}
.contact-title{left:12px;top:131px;font-size:19px;font-weight:700;color:var(--red)}
.contact-line{left:12px;font-size:8.8px;display:flex;align-items:center;gap:6px}
.contact-line svg{width:9px;height:9px}
.social{top:226px;display:flex;align-items:center;gap:4px;font-size:6.2px;font-weight:500}
.social i{display:block;width:9px;height:9px;border:1px solid var(--ink);border-radius:50%}
.outcome{width:66px;height:66px;border-radius:50%;background:var(--white);display:flex;flex-direction:column;align-items:center;justify-content:center;font-size:7px;font-weight:700;text-align:center;line-height:1.2}
.outcome svg{width:16px;height:16px;margin-bottom:3px}
</style>
</head>
<body>

<section class="slide s1">
  <h1 class="heading"><span class="red">Lead</span> Life Cycle<br>Program</h1>
  <p class="subhead">Credit Pre-Qualification and<br>Trade-In Appraisal</p>
  <svg class="cycle" viewBox="-125 -125 250 250">
    <path d="M-100 0A100 100 0 0 1 0-100L0-40A40 40 0 0 0-40 0Z" fill="var(--red)"/>
    <path d="M0-100A100 100 0 0 1 100 0L40 0A40 40 0 0 0 0-40Z" fill="var(--dark)"/>
    <path d="M100 0A100 100 0 0 1 0 100L0 40A40 40 0 0 0 40 0Z" fill="var(--red)"/>
    <path d="M0 100A100 100 0 0 1-100 0L-40 0A40 40 0 0 0 0 40Z" fill="var(--dark)"/>
    <polygon points="-3,-120 32,-70 -3,-20" fill="var(--red)"/>
    <polygon points="120,-3 70,32 20,-3" fill="var(--dark)"/>
    <polygon points="3,120 -32,70 3,20" fill="var(--red)"/>
    <polygon points="-120,3 -70,-32 -20,3" fill="var(--dark)"/>
    <circle cx="0" cy="0" r="38" fill="#fdf1ee"/>
    <g fill="none" stroke="#fff" stroke-width="1.6">
      <path d="M-57-64h20l4-6h-24zM-59-64v6h26v-6" />
      <rect x="45" y="-80" width="12" height="20" rx="2"/>
      <path d="M52-12h22v14h-22zM52-12l11 8 11-8"/>
      <circle cx="-60" cy="28" r="5"/><path d="M-70 42q10-10 20 0"/>
    </g>
    <g fill="#fff" font-family="Poppins,sans-serif" font-weight="600" font-size="10" text-anchor="middle">
      <text x="-53" y="-40">Vehicles</text>
      <text x="58" y="-37">Smartphones</text>
      <text x="40" y="58">Email</text>
      <text x="-53" y="56">Value</text>
    </g>
    <text x="0" y="0" text-anchor="middle" font-family="Poppins,sans-serif" font-weight="700" font-size="12" fill="var(--dark)">Plorven</text>
    <text x="0" y="11" text-anchor="middle" font-family="Poppins,sans-serif" font-size="5" letter-spacing="1" fill="var(--dark)">MARKETING</text>
  </svg>
</section>

<section class="slide s5">
  <div class="accent-bar center"></div>
  <h2 class="heading center">Cross-Offer Opportunities</h2>
  <p class="col-head" style="left:12px;top:62px">Cross-Offer Opportunitiesfor<br>Maximum Engagement</p>
  <div class="col-rule" style="left:79px;top:86px"></div>
  <p class="col-head" style="left:168px;top:62px">Leverage Email &amp; Social<br>Retargeting to Drive Cross-Action</p>
  <div class="col-rule" style="left:235px;top:86px"></div>
  <p class="col-head" style="left:330px;top:62px">Customer Journey Map</p>
  <div class="col-div" style="left:160px;top:63px;height:155px"></div>
  <div class="col-div" style="left:324px;top:63px;height:155px"></div>

  <p class="lead-label" style="left:12px;top:95px">Credit Lead</p>
  <p class="lead-sub" style="left:12px;top:107px">Offer Trade-In Valuation</p>
  <svg style="left:62px;top:116px;width:50px;height:70px" viewBox="0 0 50 70">
    <path d="M25 2v10M25 58v10" stroke="var(--ink)" stroke-width="1.5"/>
    <path d="M21 7l4-5 4 5zM21 63l4 5 4-5z" fill="var(--ink)"/>
    <circle cx="25" cy="35" r="19" fill="#fff" stroke="var(--ink)" stroke-width="1"/>
    <text x="25" y="33" text-anchor="middle" font-family="Poppins,sans-serif" font-size="6.5" font-weight="600" fill="var(--ink)">Start</text>
    <text x="25" y="42" text-anchor="middle" font-family="Poppins,sans-serif" font-size="6.5" font-weight="600" fill="var(--ink)">As A</text>
  </svg>
  <p class="lead-label" style="left:11px;top:183px">Trade-In Lead</p>
  <p class="lead-sub" style="left:12px;top:195px">Offer Credit Pre-Qualification</p>

  <div role="img" aria-label="Photo of a smiling man in a green jacket looking at his smartphone" style="left:213px;top:130px;width:60px;height:78px;border-radius:30px 30px 4px 4px;background:linear-gradient(180deg,#b89884 0%,#6f8050 45%,#56663c 100%)"></div>
  <svg style="left:196px;top:95px;width:100px;height:62px" viewBox="0 0 100 62">
    <g fill="#fff" stroke="var(--red)" stroke-width="1"><circle cx="47" cy="10" r="8"/><circle cx="12" cy="44" r="8"/><circle cx="85" cy="44" r="8"/></g>
    <path d="M8 41h8v6h-8zM8 41l4 3 4-3" fill="none" stroke="var(--ink)" stroke-width=".8"/>
    <text x="47" y="12.5" text-anchor="middle" font-family="Poppins,sans-serif" font-size="5" font-weight="600" fill="var(--ink)">C</text>
    <text x="85" y="46.5" text-anchor="middle" font-family="Poppins,sans-serif" font-size="5" font-weight="600" fill="var(--ink)">S</text>
    <path d="M47 19v9M18 51l7 5M79 51l-7 5" stroke="var(--red)" stroke-width="1.2"/>
    <path d="M44 26l3 4 3-4zM23 58l4 0-1-4zM74 58l-4 0 1-4z" fill="var(--red)"/>
  </svg>

  <div class="map-box" style="left:369px;top:78px"><svg viewBox="0 0 16 16" fill="none" stroke="var(--ink)" stroke-width="1"><circle cx="4" cy="4" r="2"/><circle cx="8" cy="3" r="2"/><circle cx="12" cy="4" r="2"/><path d="M6 9h4v3a2 2 0 0 1-4 0z"/></svg>Credit Lead</div>
  <div class="map-box" style="left:369px;top:130px"><svg viewBox="0 0 16 16" fill="none" stroke="var(--ink)" stroke-width="1"><rect x="2" y="3" width="12" height="9"/><path d="M5 10V7M8 10V5M11 10V8M8 12v3"/></svg>Trade-in Offer,<br>Trade-in lead</div>
  <div class="map-box" style="left:369px;top:181px"><svg viewBox="0 0 16 16" fill="none" stroke="var(--ink)" stroke-width="1"><rect x="3" y="1" width="9" height="13"/><path d="M5 5h5M5 8h5M5 11h3"/><circle cx="12.5" cy="12.5" r="2.5"/></svg>Pre-Qualification</div>
  <svg style="left:401px;top:116px;width:8px;height:68px" viewBox="0 0 8 68"><path d="M4 0v9M4 51v10" stroke="var(--ink)" stroke-width="1.3"/><path d="M0 8l4 5 4-5zM0 59l4 5 4-5z" fill="var(--ink)"/></svg>
  <p class="cta-line">Stay Top of Mind and Convert Leads into Multi-Action Customers</p>
  <div class="page-no">5</div>
</section>

<section class="slide s2">
  <div class="accent-bar center"></div>
  <h2 class="heading center">Multiple Lead Sources Feeding<br>into the Program</h2>
  <svg class="funnel" viewBox="0 0 481 270">
    <rect x="34" y="109" width="150" height="27" rx="13.5" fill="var(--red)"/>
    <path d="M174 90H342q10 0 5 9L304 147H198L168 97q-3-7 6-7z" fill="var(--red)"/>
    <rect x="290" y="166" width="167" height="26" rx="13" fill="var(--dark)"/>
    <path d="M194 154H316L262 246q-6 8-12 0z" fill="var(--dark)"/>
    <g fill="none" stroke="#fff" stroke-width="1.3">
      <circle cx="256" cy="118" r="19"/>
      <circle cx="256" cy="188" r="19"/>
      <path d="M250 125l8-9" stroke-width="3" stroke-linecap="round"/>
      <circle cx="261" cy="113" r="4" stroke-width="2"/>
      <rect x="248" y="182" width="16" height="11" fill="#fff"/>
    </g>
    <path d="M248 182l8 6 8-6" fill="none" stroke="var(--dark)" stroke-width="1.2"/>
  </svg>
  <p class="source-pill" style="left:34px;top:111px;width:130px;text-align:right">Pre-Qualification Tool<br>(Fast4Loan)- How it Works</p>
  <p class="source-note" style="left:14px;top:141px;width:150px;text-align:right">Converts Web Traffic into the<br>highest quality lead on the market</p>
  <p class="source-pill" style="left:312px;top:168px">Vorqel Email/Mail Marketing<br>How it Works</p>
  <p class="source-note" style="left:312px;top:198px;width:165px">Delivers actionable leads from email<br>marketing not Just OPENS AND CLICKS.</p>
  <p class="audience" style="left:312px;top:222px"><b>1.)</b> Past Sold Customers (Equity Targets)<br><b>2.)</b> Past Service Onlu Department Customers (Conquest Sales)<br><b>3.)</b> Unsold Leads (from previous interactions)</p>
  <div class="page-no">2</div>
</section>

<section class="slide s6">
  <div class="accent-bar"></div>
  <h2 class="heading">Continuous Engagement<br>Throughout the Lead<br>Life Cycle</h2>
  <p class="body-copy">Sed ut perspiciatis unde omnis iste natus error sit voluptatem accusantium doloremque laudantium, totam rem aperiam, eaque ipsa quae ab illo inventore veritatis et quasi architecto beatae vitae dicta sunt explicabo. Nemo enim ipsam voluptatem quia voluptas sit aspernatur aut odit aut fugit, sed quia consequuntur magni dolores eos qui ratione voluptatem sequi nesciunt.<br>Sed ut perspiciatis unde omnis iste natus error sit voluptatem accusantium doloremque laudantium, totam rem aperiam, eaque ipsa quae ab illo inventore veritatis et quasi architecto beatae vitae dicta sunt explicabo.</p>
  <svg class="cycle" viewBox="-120 -120 240 240">
    <g fill="none" stroke-width="40">
      <path d="M-77.3 20.7A80 80 0 0 1 20.7-77.3" stroke="var(--red)"/>
      <path d="M20.7-77.3A80 80 0 0 1 56.6 56.6" stroke="var(--dark)"/>
      <path d="M56.6 56.6A80 80 0 0 1-77.3 20.7" stroke="var(--grey)"/>
    </g>
    <polygon points="-108.2,29 -46.4,12.4 -79.7,-12" fill="var(--grey)"/>
    <polygon points="29,-108.2 12.4,-46.4 48,-63" fill="var(--red)"/>
    <polygon points="79.2,79.2 33.9,33.9 30,74" fill="var(--dark)"/>
    <g fill="#fff" font-family="Poppins,sans-serif" font-weight="600" font-size="9" text-anchor="middle">
      <text x="-70" y="-30">Success</text>
      <text x="75" y="-20">Start</text>
      <text x="4" y="77">Credit &amp;</text>
      <text x="4" y="87">Trade Offers</text>
    </g>
    <path d="M-72-46v-6l3-3h4l-1 4h4l-1 6h-9z" fill="none" stroke="#fff" stroke-width="1.2"/>
    <path d="M-35 76l5-5 3 3 5-6" fill="none" stroke="#fff" stroke-width="1.3"/>
    <text x="0" y="0" text-anchor="middle" font-family="Poppins,sans-serif" font-weight="700" font-size="15" fill="var(--dark)">Plorven</text>
    <text x="0" y="13" text-anchor="middle" font-family="Poppins,sans-serif" font-size="6" letter-spacing="1.4" fill="var(--dark)">MARKETING</text>
  </svg>
  <div class="page-no">6</div>
</section>

<section class="slide s3">
  <div class="accent-bar center"></div>
  <h2 class="heading center">Pre-Qualified Leads:<br>Offering Trade-In Appraisal</h2>
  <div class="flow-line" style="left:130px;width:60px;background:var(--red)"></div>
  <div class="flow-line" style="left:290px;width:60px;background:var(--dark)"></div>
  <svg class="step-ring" style="left:35px;top:107px" viewBox="0 0 100 100"><path d="M18 20A45 45 0 0 0 18 80M82 20A45 45 0 0 1 82 80" fill="none" stroke="var(--red)" stroke-width="6"/></svg>
  <svg class="step-ring" style="left:190px;top:107px" viewBox="0 0 100 100"><path d="M18 20A45 45 0 0 0 18 80M82 20A45 45 0 0 1 82 80" fill="none" stroke="var(--dark)" stroke-width="6"/></svg>
  <svg class="step-ring" style="left:347px;top:107px" viewBox="0 0 100 100"><path d="M18 20A45 45 0 0 0 18 80M82 20A45 45 0 0 1 82 80" fill="none" stroke="var(--red)" stroke-width="6"/></svg>
  <div class="step" style="left:42px;top:114px"><svg viewBox="0 0 28 28" fill="none" stroke="var(--ink)" stroke-width="1"><circle cx="11" cy="7" r="4"/><path d="M3 22q0-9 8-9"/><circle cx="18" cy="19" r="6"/><path d="M15 19l2 2 4-4"/></svg>Customer pre-qualifies<br>via Fast4Loan</div>
  <div class="step" style="left:197px;top:114px"><svg viewBox="0 0 28 28" fill="none" stroke="var(--ink)" stroke-width="1"><rect x="5" y="2" width="15" height="22"/><path d="M8 7h2M12 7h5M8 12h2M12 12h5M8 17h2M12 17h3"/><circle cx="21" cy="21" r="4.5"/><path d="M19 21l1.5 1.5 3-3"/></svg>Receives credit<br>approval</div>
  <div class="step" style="left:354px;top:114px"><svg viewBox="0 0 28 28" fill="none" stroke="var(--ink)" stroke-width="1.1"><rect x="6" y="7" width="20" height="14"/><path d="M6 7l10 8 10-8M1 11h4M2 15h3M3 19h2"/></svg>Email and Mail Example<br>to check trade-in<br>value</div>
  <div class="page-no">3</div>
</section>

<section class="slide s7">
  <div class="photo" role="img" aria-label="Photo of a dealership salesperson handing car keys to a smiling customer at a desk"></div>
  <div class="accent-bar"></div>
  <h2 class="heading">Converting Leads<br>into Sales</h2>
  <p class="body-copy">Sed ut perspiciatis unde omnis iste natus error sit voluptatem accusantium doloremque laudantium, totam rem aperiam, eaque ipsa quae ab illo inventore veritatis et quasi architecto beatae vitae dicta sunt explicabo. Nemo enim ipsam voluptatem quia voluptas sit aspernatur aut odit aut fugit, sed quia consequuntur magni dolores eos qui ratione voluptatem sequi nesciunt.</p>
  <div class="stat-card" style="left:240px"><svg viewBox="0 0 16 14" fill="var(--red)"><path d="M3 5l2-4h6l2 4h2v5h-2v2h-2v-2H5v2H3v-2H1V5z"/></svg><p class="stat-num">210+</p><p class="stat-label">Perspiciatis<br>Unde</p></div>
  <div class="stat-card" style="left:319px"><svg viewBox="0 0 16 14" fill="var(--red)"><path d="M1 0h1v13h14v1H1z"/><rect x="4" y="6" width="2" height="6"/><rect x="7" y="3" width="2" height="9"/><rect x="10" y="7" width="2" height="5"/><rect x="13" y="4" width="2" height="8"/></svg><p class="stat-num">50%</p><p class="stat-label">Perspiciatis<br>Unde</p></div>
  <div class="stat-card" style="left:398px"><svg viewBox="0 0 16 14" fill="var(--red)"><rect x="1" y="6" width="3" height="8"/><path d="M5 6l4-6q2 0 2 2l-1 3h5l-1 9H5z"/></svg><p class="stat-num">85+</p><p class="stat-label">Perspiciatis<br>Unde</p></div>
  <div class="page-no">7</div>
</section>

<section class="slide s4">
  <div class="accent-bar"></div>
  <h2 class="heading">Trade-In Leads:Offering<br>Credit Pre-Qualification</h2>
  <svg style="left:6px;top:76px;width:60px;height:190px" viewBox="0 0 60 190">
    <path d="M3 31A27 27 0 0 0 57 31" fill="none" stroke="var(--ink)" stroke-width="2"/>
    <path d="M3 91A27 27 0 0 0 57 91" fill="none" stroke="var(--green)" stroke-width="2"/>
    <path d="M3 153A27 27 0 0 0 57 153" fill="none" stroke="var(--red)" stroke-width="2"/>
    <path d="M30 58v6M30 118v8" stroke="var(--ink)" stroke-width="1.5"/>
  </svg>
  <div class="journey-node" style="left:9px;top:80px"><svg viewBox="0 0 26 26" fill="none" stroke="var(--ink)" stroke-width="1.1"><rect x="7" y="2" width="12" height="22" rx="2"/><rect x="11" y="8" width="10" height="7"/><path d="M13 10h6M13 12.5h4"/></svg></div>
  <div class="journey-node" style="left:9px;top:140px"><svg viewBox="0 0 26 26" fill="none" stroke="var(--green)" stroke-width="1.1"><path d="M3 23h20M6 22v-6M10 22v-9M14 22v-5M18 22v-11"/><path d="M5 12l5-5 4 4 7-7"/></svg></div>
  <div class="journey-node" style="left:9px;top:202px"><svg viewBox="0 0 26 26" fill="none" stroke="var(--red)" stroke-width="1.1"><circle cx="13" cy="7" r="5"/><path d="M13 4v6M3 19l5-4 5 3 5-3 5 4-5 4H8z"/></svg></div>
  <p class="journey-label" style="left:76px;top:97px">Customer texts for<br>vehicle value</p>
  <p class="journey-label" style="left:76px;top:157px;color:var(--green)">Receives trade-in<br>appraisal</p>
  <p class="journey-label" style="left:76px;top:218px;color:var(--red)">Offer to pre-qualify for<br>financing</p>
  <div role="img" aria-label="Photo of a smiling bearded man in glasses and a grey sweater looking at his phone" style="left:282px;top:18px;width:190px;height:252px;border-radius:80px 80px 0 0;background:linear-gradient(180deg,#6b4a3a 0%,#a57a62 30%,#6d6d70 55%,#55565a 100%)"></div>
  <div class="thought" style="left:202px;top:84px;width:70px;height:48px">Pre-qualify<br>for a loan</div>
  <svg style="left:245px;top:133px;width:30px;height:30px" viewBox="0 0 30 30"><ellipse cx="11" cy="7" rx="11" ry="6" fill="var(--red)"/><ellipse cx="23" cy="24" rx="5" ry="3.5" fill="var(--red)"/></svg>
  <div class="page-no">4</div>
</section>

<section class="slide s8">
  <div class="accent-bar"></div>
  <h2 class="heading">Maximize Lead Potential with<br>Cross-Offer Opportunities</h2>
  <p class="body-copy">Sed ut perspiciatis unde omnis iste natus error sit voluptatem accusantium doloremque laudantium, totam rem aperiam, eaque ipsa quae ab illo inventore veritatis et quasi architecto beatae vitae dicta sunt explicabo. Nemo enim ipsam voluptatem quia voluptas sit aspernatur aut odit aut fugit, sed quia consequuntur magni dolores eos qui ratione voluptatem sequi nesciunt.</p>
  <p class="contact-title">Contact Us</p>
  <p class="contact-line" style="top:163px"><svg viewBox="0 0 10 10" fill="var(--red)"><path d="M5 0a3.5 3.5 0 0 1 3.5 3.5C8.5 6 5 10 5 10S1.5 6 1.5 3.5A3.5 3.5 0 0 1 5 0z"/><circle cx="5" cy="3.5" r="1.3" fill="var(--slide)"/></svg>48 Harlow Lane Suite 210, Brookvale 20415, United States</p>
  <p class="contact-line" style="top:183px"><svg viewBox="0 0 10 10" fill="var(--red)"><path d="M2 0h2l1 3-1.5 1q1 2 2.5 2.5L7 5l3 1v2q0 2-2 2Q0 9 0 2q0-2 2-2z"/></svg>+1-555-014-2290</p>
  <p class="contact-line" style="top:203px"><svg viewBox="0 0 10 10" fill="var(--red)"><rect x="0" y="2" width="10" height="7"/><path d="M0 2l5 4 5-4" fill="none" stroke="var(--slide)" stroke-width="1"/></svg>hello@plorvenads.example</p>
  <p class="social" style="left:12px"><i></i>Chatterbook</p>
  <p class="social" style="left:70px"><i></i>Linkora</p>
  <p class="social" style="left:116px"><i></i>Snapgrove</p>
  <svg style="left:365px;top:22px;width:72px;height:242px" viewBox="0 0 72 242">
    <path d="M2 38A34 34 0 0 0 70 38M2 116A34 34 0 0 0 70 116M2 196A34 34 0 0 0 70 196" fill="none" stroke="var(--red)" stroke-width="2.2"/>
    <path d="M36 72v6M36 150v10" stroke="var(--ink)" stroke-width="2"/>
  </svg>
  <div class="outcome" style="left:368px;top:27px"><svg viewBox="0 0 16 16" fill="none" stroke="var(--red)" stroke-width="1"><circle cx="4" cy="4" r="2"/><circle cx="8" cy="3" r="2"/><circle cx="12" cy="4" r="2"/><path d="M6 9h4v3a2 2 0 0 1-4 0z"/></svg>Credit<br>Leads</div>
  <div class="outcome" style="left:368px;top:105px"><svg viewBox="0 0 16 16" fill="none" stroke="var(--red)" stroke-width="1"><rect x="2" y="4" width="12" height="8"/><path d="M5 10V8M8 10V6M11 10V7M8 12v3M4 3l2-2 2 2 2-2 2 2"/></svg>Trade<br>Leads</div>
  <div class="outcome" style="left:368px;top:185px"><svg viewBox="0 0 16 16" fill="none" stroke="var(--red)" stroke-width="1"><circle cx="8" cy="4" r="3"/><path d="M6.5 4l1 1 2-2"/><circle cx="3" cy="10" r="1.8"/><circle cx="8" cy="10" r="1.8"/><circle cx="13" cy="10" r="1.8"/><path d="M1 15q2-3 4 0M6 15q2-3 4 0M11 15q2-3 4 0"/></svg>Successful<br>Customer<br>Outcomes</div>
</section>

</body>
</html>
```